RESIDENTIAL CONSTRUCTION

We are a company that specializes in building custom residential homes, the design should also emphasize that quality and service is our priority.

Industry/Entity Type

Construction Company

Contact Information for Business Card

Contact Person: Marcus Lindqvist
Company Address: 273 West Alder Ave San Jose , Ca 95380
Phone Number : 408-731-2946
Email Address: Stoneridgehomes517@mailvista.net

Font styles to use
Sans Serif

Colors
ec1f27

Requirements
Must have
• CSLB # 7362015
Nice to have
• needs to have same color as logo i uploaded, we will be printing these on a clear plastic card.

```html
<!DOCTYPE html>
<html lang="en">
<head>
<meta charset="utf-8">
<title>Stoneridge Homes – Business Card</title>
<link rel="stylesheet" href="https://fonts.googleapis.com/css2?family=Oswald:wght@600&family=Arimo:wght@400&display=swap">
<style>
  :root {
    --backdrop: #38383a;
    --card-black: #0a0a0b;
    --card-white: #ffffff;
    --blush: #efc3b6;
    --brand-red: #ec1f27;
    --ink: #1a1a1a;
  }
  * { margin: 0; padding: 0; box-sizing: border-box; }
  html, body { width: 1200px; height: 1200px; overflow: hidden; }
  body {
    background: var(--backdrop);
    position: relative;
    font-family: "Arimo", Arial, sans-serif;
  }
  .card {
    position: absolute;
    left: 250px;
    width: 700px;
    height: 400px;
    box-shadow: 0 12px 30px rgba(0,0,0,0.45);
  }
  .card-front {
    top: 150px;
    background: var(--card-black);
    display: flex;
    align-items: center;
    justify-content: center;
  }
  .card-back {
    top: 650px;
    background: linear-gradient(180deg, var(--card-white) 0%, var(--card-white) 52%, var(--blush) 100%);
  }
  .brand {
    display: flex;
    align-items: center;
    gap: 14px;
  }
  .brand-square {
    width: 34px;
    height: 34px;
    background: var(--brand-red);
  }
  .brand-name {
    font-family: "Oswald", "Arial Narrow", sans-serif;
    font-weight: 600;
    color: var(--brand-red);
    font-size: 56px;
    letter-spacing: 1px;
    line-height: 1;
    text-transform: uppercase;
  }
  .card-back .brand {
    position: absolute;
    left: 60px;
    top: 140px;
  }
  .card-back .brand-name { font-size: 50px; }
  .contact-name {
    position: absolute;
    right: 50px;
    top: 48px;
    font-size: 32px;
    letter-spacing: 0.5px;
    color: var(--ink);
    text-transform: uppercase;
  }
  .contact-name .surname { color: var(--brand-red); }
  .address {
    position: absolute;
    left: 150px;
    top: 226px;
    font-size: 21px;
    font-style: normal;
    line-height: 1.3;
    color: var(--ink);
  }
  .contact-lines {
    position: absolute;
    left: 150px;
    top: 290px;
    list-style: none;
    font-size: 21px;
    color: var(--ink);
  }
  .contact-lines li {
    display: flex;
    align-items: center;
    gap: 14px;
    height: 29px;
  }
  .contact-lines svg { width: 20px; height: 20px; fill: var(--brand-red); flex: none; }
  .license-mark {
    width: 20px;
    height: 20px;
    flex: none;
    display: flex;
    align-items: center;
    justify-content: center;
  }
  .license-mark::before {
    content: "";
    width: 10px;
    height: 10px;
    background: var(--brand-red);
  }
</style>
</head>
<body>

<section class="card card-front" aria-label="Card front">
  <div class="brand">
    <span class="brand-square"></span>
    <span class="brand-name">Stoneridge Homes</span>
  </div>
</section>

<section class="card card-back" aria-label="Card back">
  <p class="contact-name">Marcus <span class="surname">Lindqvist</span></p>

  <div class="brand">
    <span class="brand-square"></span>
    <span class="brand-name">Stoneridge Homes</span>
  </div>

  <address class="address">
    273 West Alder Ave<br>
    San Jose , Ca 95380
  </address>

  <ul class="contact-lines">
    <li>
      <svg viewBox="0 0 24 24" aria-hidden="true"><path d="M6.6 10.8a15.1 15.1 0 0 0 6.6 6.6l2.2-2.2a1 1 0 0 1 1-.25 11.4 11.4 0 0 0 3.6.57 1 1 0 0 1 1 1V20a1 1 0 0 1-1 1A17 17 0 0 1 3 4a1 1 0 0 1 1-1h3.5a1 1 0 0 1 1 1c0 1.25.2 2.45.57 3.57a1 1 0 0 1-.25 1z"/></svg>
      <span>408-731-2946</span>
    </li>
    <li>
      <svg viewBox="0 0 24 24" aria-hidden="true"><path d="M2 5h20v14H2z M3.5 6.5l8.5 6.5 8.5-6.5" fill="none" stroke="#ec1f27" stroke-width="2"/></svg>
      <span>Stoneridgehomes517@mailvista.net</span>
    </li>
    <li>
      <span class="license-mark" aria-hidden="true"></span>
      <span>CSLB # 7362015</span>
    </li>
  </ul>
</section>

</body>
</html>
```